KORVEN Medical needs bold attention catching website for healthcare professionals(target)

I need a hero page as well as a products and about page for a website of mine. I specialize in orthopedic instruments . Specifically bone drills and saws. This whole company was founded to bring superb quality highly discounted medical instruments. Specifically bone drills, bone saws, k-wires and pins. Two main points should be cost savings and superior quality.

Target Market(s)

healthcare professionals Surgeons and hospital material managers

Number of Pages Required

3 page

Font styles to use
Serif

Colors

Designer to choose colors to be used in the design.

Requirements
Must have
• colors should match logo design

```html
<!DOCTYPE html>
<html lang="en">
<head>
<meta charset="utf-8">
<title>KORVEN Medical</title>
<link href="https://fonts.googleapis.com/css2?family=Merriweather:wght@400;700&family=Open+Sans:wght@400;600&display=swap" rel="stylesheet">
<style>
:root{
  --orange:#f7901e;
  --ink:#1b1b1b;
  --dark:#1a1a1a;
  --ring:#ececec;
  --muted:#555;
  --white:#fff;
  --hero-a:#f4f4f4;
  --hero-b:#dcdcdc;
  --field:#e6e6e6;
}
*{margin:0;padding:0;box-sizing:border-box}
html,body{width:1200px;height:2880px;overflow:hidden;background:var(--white)}
body{position:relative;font-family:'Open Sans',sans-serif;color:var(--ink)}
.abs{position:absolute}
.serif{font-family:'Merriweather',serif}

/* hero */
.hero{left:0;top:0;width:1200px;height:680px;background:linear-gradient(100deg,var(--hero-b) 0%,var(--hero-a) 45%,#fafafa 100%)}
.hero-photo{left:626px;top:90px;width:392px;height:553px;border-radius:180px 180px 0 0;background:linear-gradient(180deg,#c9c9c9 0%,#e9e9e9 40%,#f2f2f2 100%)}
.hero-curve{left:0;top:560px}
.logo{left:173px;top:40px;display:flex;align-items:center;gap:8px;font-family:'Merriweather',serif;font-size:21px;color:var(--ink)}
.logo-dot{width:14px;height:14px;border-radius:50%;background:var(--orange)}
.nav a{position:absolute;top:48px;font-family:'Merriweather',serif;font-size:11px;letter-spacing:1px;color:var(--ink);text-decoration:none;font-weight:700}
.nav .active{color:var(--orange)}
.nav .active::after{content:"";position:absolute;left:4px;right:4px;top:22px;height:2px;background:var(--orange)}
.hero-title{left:172px;top:212px;font-size:33px;line-height:56px;font-weight:700;letter-spacing:.5px}
.save{left:172px;top:328px;font-size:21px;font-weight:700}
.save span{color:var(--orange);font-size:38px;margin-left:8px}
.btn{display:flex;align-items:center;justify-content:center;border-radius:24px;font-family:'Merriweather',serif;font-weight:700;text-decoration:none}
.btn-dark{background:var(--ink);color:var(--white)}
.btn-orange{background:var(--orange);color:var(--white);font-size:13px}
.order{left:172px;top:400px;width:197px;height:45px;font-size:16px;gap:10px}

/* products */
.section-title{left:0;width:1200px;text-align:center;font-size:24px;font-weight:700;letter-spacing:2px}
.rule{height:3px;background:var(--orange)}
.product{width:220px;text-align:center}
.ring{width:164px;height:164px;border-radius:50%;border:12px solid var(--ring);margin:0 auto;position:relative}
.ring.on{border-color:var(--orange)}
.item{position:absolute;background:linear-gradient(180deg,#d7d7d7,#9a9a9a);border-radius:4px}
.p-name{font-family:'Merriweather',serif;font-weight:700;font-size:13px;line-height:21px;margin-top:52px;letter-spacing:.4px}
.p-price{font-family:'Merriweather',serif;font-weight:700;font-size:13px;color:var(--orange);margin-top:5px;letter-spacing:.5px}

/* about */
.about{left:0;top:1649px;width:1200px;height:481px;background:var(--dark)}
.about-photo{left:173px;top:1717px;width:344px;height:344px;border-radius:50%;border:22px solid var(--orange);background:linear-gradient(180deg,#f4f4f4,#cfcfcf)}
.about-h{left:611px;top:1735px;color:var(--white);font-size:24px;font-weight:700;letter-spacing:1.5px}
.about-p{left:612px;width:420px;color:#e9e9e9;font-size:12.5px;line-height:24px}
.about-p b{color:var(--orange);font-weight:600}

/* form */
.msg-h{left:0;width:1200px;top:2196px;text-align:center;font-size:24px;font-weight:700}
.field{border:1px solid var(--field);font-size:11px;color:#aaa;padding:8px 12px;background:var(--white)}
.field.focus{border-color:#333}

/* footer */
.footer{left:0;top:2616px;width:1200px;height:264px;background:var(--dark);color:var(--white)}
.f-head{font-family:'Merriweather',serif;font-weight:700;font-size:14px}
.f-link{font-size:10px;color:var(--white)}
.card{width:33px;height:19px;border-radius:2px}
.social{width:26px;height:26px;border-radius:50%}
</style>
</head>
<body>

<div class="abs hero"></div>
<div class="abs hero-photo" role="img" aria-label="Smiling doctor in white coat with stethoscope, arms crossed"></div>
<svg class="abs hero-curve" width="1200" height="130" viewBox="0 0 1200 130" aria-hidden="true">
  <path d="M0 18 Q600 150 1200 18 L1200 130 L0 130Z" fill="#fff"/>
  <path d="M0 18 Q300 82 600 88" stroke="#f7901e" stroke-width="9" fill="none"/>
  <path d="M600 88 Q900 82 1200 18" stroke="#1b1b1b" stroke-width="7" fill="none"/>
</svg>

<div class="abs logo"><span class="logo-dot"></span>KORVEN Medical</div>
<nav class="nav">
  <a class="active" style="left:572px">HOME</a>
  <a style="left:675px">PRODUCTS</a>
  <a style="left:799px">CONTACT US</a>
</nav>
<svg class="abs" style="left:972px;top:46px" width="16" height="16" viewBox="0 0 16 16" aria-label="Search"><circle cx="6.5" cy="6.5" r="5" fill="none" stroke="#f7901e" stroke-width="1.6"/><path d="M10.2 10.2 15 15" stroke="#f7901e" stroke-width="1.6"/></svg>
<svg class="abs" style="left:1011px;top:44px" width="16" height="18" viewBox="0 0 16 18" aria-label="Cart"><rect x="1.5" y="6" width="13" height="11" fill="none" stroke="#f7901e" stroke-width="1.6"/><path d="M5 8V4a3 3 0 0 1 6 0v4" fill="none" stroke="#f7901e" stroke-width="1.6"/></svg>

<h1 class="abs hero-title serif">High-Quality Products at a<br>Significantly Lower Cost</h1>
<p class="abs save serif">save up to<span>50%-60%</span></p>
<a class="abs btn btn-dark order">Order Now <svg width="26" height="8" viewBox="0 0 26 8"><path d="M0 4h24M20 1l4 3-4 3" stroke="#fff" stroke-width="1.2" fill="none"/></svg></a>

<svg class="abs" style="left:568px;top:547px" width="64" height="134" viewBox="0 0 64 134" aria-label="Scroll down">
  <circle cx="32" cy="32" r="29" fill="none" stroke="#f7901e" stroke-width="1.5"/>
  <circle cx="32" cy="32" r="21" fill="none" stroke="#f7901e" stroke-width="1.5"/>
  <rect x="27" y="23" width="10" height="16" rx="5" fill="none" stroke="#1b1b1b" stroke-width="1.4"/>
  <line x1="32" y1="27" x2="32" y2="31" stroke="#1b1b1b" stroke-width="1.4"/>
  <line x1="32" y1="39" x2="32" y2="133" stroke="#1b1b1b" stroke-width="1.4"/>
</svg>

<h2 class="abs section-title serif" style="top:718px">PRODUCTS</h2>
<div class="abs rule" style="left:575px;top:757px;width:52px"></div>

<!-- row 1 -->
<div class="abs product" style="left:158px;top:827px">
  <div class="ring on"><div class="item" role="img" aria-label="K-wire pins" style="left:60px;top:-30px;width:20px;height:200px;background:linear-gradient(90deg,#bbb,#eee,#aaa)"></div></div>
  <a class="btn btn-orange" style="width:144px;height:37px;margin:56px auto 0">Buy Now</a>
</div>
<div class="abs product" style="left:380px;top:827px">
  <div class="ring"><div class="item" role="img" aria-label="Bone drill bit" style="left:-8px;top:68px;width:168px;height:6px"></div></div>
  <p class="p-name">Product Title Here</p><p class="p-price">$25.00</p>
</div>
<div class="abs product" style="left:600px;top:827px">
  <div class="ring"><div class="item" role="img" aria-label="Intramedullary nail" style="left:-8px;top:66px;width:180px;height:8px"></div></div>
  <p class="p-name">Intramedullary Nail<br>Femur</p><p class="p-price">$5.00-$35.00</p>
</div>
<div class="abs product" style="left:818px;top:827px">
  <div class="ring"><div class="item" role="img" aria-label="Bone drill" style="left:30px;top:40px;width:95px;height:110px"></div></div>
  <p class="p-name">Bone Drill</p><p class="p-price">$5.00-$35.00</p>
</div>

<!-- row 2 -->
<div class="abs product" style="left:162px;top:1181px">
  <div class="ring"><div class="item" role="img" aria-label="Oscillating saw" style="left:40px;top:40px;width:90px;height:90px"></div></div>
  <p class="p-name">Oscillating Saw</p><p class="p-price">$5.00-$35.00</p>
</div>
<div class="abs product" style="left:380px;top:1181px">
  <div class="ring"><div class="item" role="img" aria-label="Bone drill bit" style="left:-8px;top:68px;width:168px;height:6px"></div></div>
  <p class="p-name">Product Title here</p><p class="p-price">$25.00</p>
</div>
<div class="abs product" style="left:600px;top:1181px">
  <div class="ring"><div class="item" role="img" aria-label="Electric oscillating saw set" style="left:10px;top:40px;width:140px;height:90px"></div></div>
  <p class="p-name">Electric Oscillating<br>Saw</p><p class="p-price">$550.00</p>
</div>
<div class="abs product" style="left:818px;top:1181px">
  <div class="ring"><div class="item" role="img" aria-label="Bone drill" style="left:30px;top:40px;width:95px;height:110px"></div></div>
  <p class="p-name">Bone Drill</p><p class="p-price">$5.00-$35.00</p>
</div>

<a class="abs btn btn-orange" style="left:528px;top:1535px;width:145px;height:37px">View All</a>

<!-- about -->
<div class="abs about"></div>
<div class="abs about-photo" role="img" aria-label="Smiling nurse in dark scrubs, arms crossed"></div>
<h2 class="abs about-h serif">ABOUT</h2>
<div class="abs rule" style="left:612px;top:1774px;width:48px"></div>
<p class="abs about-p" style="top:1806px"><b>KORVEN Medical</b> was created to offer hospitals and physicians high-quality products at a significantly lower cost.</p>
<p class="abs about-p" style="top:1878px"><b>KORVEN Medical</b> focus is on the orthopedic disposable market by providing quality generic products that are utilized to replace many legacy products thatt have low physician preference and are subject to 5%-10% annual unsustainable price increases.</p>
<a class="abs btn btn-orange" style="left:610px;top:2001px;width:145px;height:37px">Read More</a>
<div class="abs" style="left:599px;top:2086px;width:2px;height:90px;background:var(--orange)"></div>

<!-- message form -->
<h2 class="abs msg-h serif">Send us a Message</h2>
<div class="abs field focus" style="left:358px;top:2258px;width:231px;height:29px">First Name</div>
<div class="abs field" style="left:610px;top:2258px;width:232px;height:29px">Last Name</div>
<div class="abs field" style="left:358px;top:2306px;width:231px;height:29px">Email</div>
<div class="abs field" style="left:610px;top:2306px;width:232px;height:29px">Phone</div>
<div class="abs field" style="left:358px;top:2354px;width:484px;height:132px">Message</div>
<a class="abs btn btn-dark" style="left:361px;top:2508px;width:481px;height:49px;border-radius:25px;font-size:13px">Send Message</a>

<!-- footer -->
<div class="abs footer"></div>
<div class="abs logo" style="top:2668px;color:var(--white)"><span class="logo-dot"></span>KORVEN Medical</div>
<p class="abs f-head" style="left:392px;top:2645px;color:#fff">Info</p>
<p class="abs f-link" style="left:392px;top:2677px;color:var(--orange)">Home</p>
<p class="abs f-link" style="left:392px;top:2700px">About</p>
<p class="abs f-link" style="left:392px;top:2722px">Products</p>
<p class="abs f-link" style="left:392px;top:2744px">Contact</p>
<p class="abs f-head" style="left:610px;top:2645px;color:#fff">Connect</p>
<p class="abs f-link" style="left:611px;top:2677px">(555) 014-2290</p>
<p class="abs f-link" style="left:611px;top:2700px">info@korvenmedical.com</p>
<div class="abs social" style="left:611px;top:2746px;background:var(--orange)" aria-label="Social link"></div>
<div class="abs social" style="left:660px;top:2746px;background:#fff" aria-label="Social link"></div>
<div class="abs social" style="left:708px;top:2746px;background:#fff" aria-label="Social link"></div>
<div class="abs card" style="left:829px;top:2649px;background:#2a6fb5" aria-label="Payment method"></div>
<div class="abs card" style="left:869px;top:2649px;background:#f2f2f2" aria-label="Payment method"></div>
<div class="abs card" style="left:909px;top:2649px;background:#3aa0dc" aria-label="Payment method"></div>
<div class="abs card" style="left:949px;top:2649px;background:#f2f2f2" aria-label="Payment method"></div>
<div class="abs card" style="left:989px;top:2649px;background:#e4e4e4" aria-label="Payment method"></div>
<p class="abs f-link" style="left:171px;top:2828px">© 2019 KORVENMEDICAL</p>

</body>
</html>
```